Elegant Business Card for Technology Company

Client is a supplier of innovative industrial communications and automation equipment since 2002. This contest is to gather fresh ideas for a redesign of the existing business card. Client is looking for design that best communicates tagline "Industrial Networking and Computing Specialist".

Design submissions should look modern, clean, elegant and professional. It should not be cluttered. Use white as the primary colour. Orange and black as secondary colour. Refer to jpeg File 1 on the current design.

Fonts used by Client used include Arial Regular, Arial Black, Roboto Regular, Roboto Black and Lato.

The winning design will be sent for offset printing using super white 250gsm artcard paper (open for suggestions).

Target Market(s)

System Engineers, Project Managers, Purchasing Managers from companies providing engineering services for Smart Cities.

Industry/Entity Type

Information Technology

Contact Information for Business Card

Refer to PDF File 3 for Business Card Details. Priority of short contact information would be as follows Name > Job Title > Email > Mobile > Web > Tel > Fax > Business Address >UEN (UEN represents company registration number)

Font styles to use
Sans Serif

Colors
ffffff
f37122
000000
5c5c5c

Requirements
Must have
• Refer to AI File 2 (Company Logo) & PDF File 3 (Information on Namecard)
Should not have
• No QR codes
• No Social Media Icons
• Do not create full Black or Orange colour background

```html
<!DOCTYPE html>
<html lang="en">
<head>
<meta charset="utf-8">
<title>KVR Business Card</title>
<link rel="stylesheet" href="https://fonts.googleapis.com/css2?family=Open+Sans:wght@400;600;700&display=swap">
<style>
  :root {
    --white: #ffffff;
    --orange: #f37122;
    --black: #000000;
    --grey: #5c5c5c;
    --charcoal-deep: #2a2a2a;
    --charcoal-light: #4a4a4a;
    --backdrop: #8f8f8f;
    --tagline: #f0f0f0;
  }
  * { margin: 0; padding: 0; box-sizing: border-box; }
  html, body {
    width: 1105px;
    height: 1200px;
    overflow: hidden;
  }
  body {
    background: var(--backdrop);
    font-family: "Open Sans", Arial, sans-serif;
    position: relative;
  }
  .card {
    position: absolute;
    left: 182px;
    width: 747px;
    height: 425px;
    overflow: hidden;
  }
  /* Front */
  .card--front { top: 119px; background: var(--white); }
  .brand {
    position: absolute;
    left: 420px;
    top: 52px;
    display: flex;
    align-items: center;
    gap: 18px;
  }
  .brand__dot {
    width: 96px;
    height: 96px;
    border-radius: 50%;
    background: var(--orange);
  }
  .brand__name {
    font-weight: 700;
    font-size: 92px;
    line-height: 1;
    color: var(--black);
    letter-spacing: 2px;
  }
  .edge-tab {
    position: absolute;
    left: -28px;
    top: 196px;
    width: 40px;
    height: 56px;
    border-radius: 50%;
    background: var(--orange);
  }
  .person {
    position: absolute;
    left: 44px;
    top: 194px;
  }
  .person__name {
    font-size: 27px;
    font-weight: 600;
    color: var(--orange);
    line-height: 1.2;
  }
  .person__title {
    font-size: 19px;
    color: var(--black);
    line-height: 1.3;
  }
  .divider {
    position: absolute;
    left: 44px;
    right: 44px;
    top: 264px;
    height: 1.5px;
    background: var(--orange);
  }
  .contacts {
    position: absolute;
    left: 44px;
    top: 282px;
    list-style: none;
  }
  .contacts__item {
    display: flex;
    align-items: center;
    height: 28px;
    font-size: 19px;
    color: var(--grey);
  }
  .contacts__icon {
    width: 18px;
    height: 18px;
    margin-right: 13px;
    fill: var(--orange);
  }
  .address {
    position: absolute;
    right: 44px;
    top: 282px;
    text-align: right;
    font-style: normal;
    font-size: 19px;
    color: var(--grey);
  }
  .address__line { height: 28px; line-height: 28px; display: block; }
  .address__web { color: var(--orange); letter-spacing: 1px; }
  .footer-bars {
    position: absolute;
    left: 0;
    bottom: 0;
    width: 747px;
    height: 13px;
  }
  /* Back: charcoal gradient rather than a solid black field */
  .card--back {
    top: 637px;
    background: linear-gradient(135deg, var(--charcoal-deep) 0%, var(--charcoal-light) 55%, var(--charcoal-deep) 100%);
  }
  .back-texture {
    position: absolute;
    inset: 0;
    background:
      radial-gradient(circle at 5% 10%, rgba(243,113,34,0.2), transparent 18%),
      radial-gradient(circle at 95% 10%, rgba(243,113,34,0.18), transparent 14%),
      radial-gradient(circle at 90% 85%, rgba(243,113,34,0.16), transparent 20%),
      radial-gradient(circle at 5% 88%, rgba(243,113,34,0.14), transparent 12%);
  }
  .back-brand {
    position: absolute;
    left: 0;
    right: 0;
    top: 118px;
    text-align: center;
    font-weight: 700;
    font-size: 100px;
    line-height: 1;
    color: var(--white);
    letter-spacing: 3px;
  }
  .tagline {
    position: absolute;
    left: 0;
    right: 0;
    top: 290px;
    text-align: center;
    font-size: 19px;
    line-height: 26px;
    color: var(--tagline);
  }
</style>
</head>
<body>

<section class="card card--front" aria-label="Business card front">
  <div class="brand">
    <span class="brand__dot"></span>
    <span class="brand__name">KVR</span>
  </div>

  <span class="edge-tab"></span>

  <div class="person">
    <p class="person__name">Daniel Koh</p>
    <p class="person__title">Sales Manager</p>
  </div>

  <div class="divider"></div>

  <ul class="contacts">
    <li class="contacts__item">
      <svg class="contacts__icon" viewBox="0 0 24 24" aria-hidden="true"><path d="M6.6 10.8c1.4 2.8 3.8 5.1 6.6 6.6l2.2-2.2c.3-.3.7-.4 1-.2 1.1.4 2.3.6 3.6.6.6 0 1 .4 1 1V20c0 .6-.4 1-1 1C10.6 21 3 13.4 3 4c0-.6.4-1 1-1h3.5c.6 0 1 .4 1 1 0 1.3.2 2.5.6 3.6.1.3 0 .7-.2 1L6.6 10.8z"/></svg>
      +65 6100 2040
    </li>
    <li class="contacts__item">
      <svg class="contacts__icon" viewBox="0 0 24 24" aria-hidden="true"><path d="M7 1h10a2 2 0 0 1 2 2v18a2 2 0 0 1-2 2H7a2 2 0 0 1-2-2V3a2 2 0 0 1 2-2zm0 3v14h10V4H7zm5 15.5a1 1 0 1 0 0 2 1 1 0 0 0 0-2z"/></svg>
      +65 9100 3050
    </li>
    <li class="contacts__item">
      <svg class="contacts__icon" viewBox="0 0 24 24" aria-hidden="true"><path d="M6 2h12v5H6zM3 8h18a2 2 0 0 1 2 2v7h-4v5H5v-5H1v-7a2 2 0 0 1 2-2zm4 7v5h10v-5H7z"/></svg>
      +65 6100 2041
    </li>
    <li class="contacts__item">
      <svg class="contacts__icon" viewBox="0 0 24 24" aria-hidden="true"><path d="M2 5h20v2l-10 6L2 7V5zm0 4.3l10 6 10-6V19H2V9.3z"/></svg>
      sales@kvr-tech.sg
    </li>
  </ul>

  <address class="address">
    <span class="address__line">25 Kallang Way</span>
    <span class="address__line">Tech Hub #04-12 (Block B)</span>
    <span class="address__line">Singapore 349201</span>
    <span class="address__line address__web">www.kvr-tech.sg</span>
  </address>

  <svg class="footer-bars" viewBox="0 0 747 13" preserveAspectRatio="none" aria-hidden="true">
    <polygon points="0,0 491,0 487,13 0,13" fill="var(--black)"/>
    <polygon points="498,0 747,0 747,13 494,13" fill="var(--orange)"/>
  </svg>
</section>

<section class="card card--back" aria-label="Business card back">
  <div class="back-texture" role="img" aria-label="Faint dotted circle pattern in dark orange tones"></div>
  <p class="back-brand">KVR</p>
  <p class="tagline">
    Industrial Networking &amp; Computing Specialist<br>
    Industrial Ethernet / Wireless / Cellular<br>
    Industrial &amp; Embedded Computing / Serial / Fieldbus Connectivity<br>
    IP Video Surveillance / Remote Automation
  </p>
</section>

</body>
</html>
```